Treatment Info-Graphic Poster

22 x 28 poster. We need a design for a poster to hang in our treatment rooms that quickly compares different treatments we offer and sets expectations for the patient. Attached is something I very quickly created on Excel, but we would like one that matches our company colors and looks much more polished. I have attached a info-graphic we have had designed prior for reference.

Target Market(s)

Osteoarthritis of the knee patients treatment comparison info graphic for poster

Font styles to use
Serif

Colors
85cae6
f78f20

Requirements
Must have
• Branded treatment comparison table
Nice to have
• Treatment graphics

```html
<!DOCTYPE html>
<html lang="en">
<head>
<meta charset="utf-8">
<title>Knee OA Treatment Comparison</title>
<link rel="stylesheet" href="https://fonts.googleapis.com/css2?family=Zilla+Slab:wght@500;600;700&family=Mulish:wght@400;600;700&display=swap">
<style>
  :root{
    --orange:#f7941d;
    --teal:#42a6bf;
    --label:#5d5d60;
    --ink:#555558;
    --head-bg:#f7f7f7;
    --body-bg:#e1f2fb;
    --white:#ffffff;
  }
  *{margin:0;padding:0;box-sizing:border-box}
  html,body{width:1200px;height:848px;overflow:hidden}
  body{position:relative;background:var(--body-bg);font-family:"Mulish",sans-serif;color:var(--ink)}
  .masthead{position:absolute;left:0;top:0;width:1200px;height:175px;background:var(--head-bg)}
  .brand{position:absolute;left:80px;top:50px;display:flex;align-items:center;gap:10px}
  .brand-mark{width:18px;height:18px;background:var(--teal)}
  .brand-name{font-family:"Zilla Slab",serif;font-weight:700;font-size:56px;line-height:1;color:var(--teal)}
  .brand-tagline{position:absolute;left:108px;top:136px;font-size:15px;color:#333}
  .title{position:absolute;left:311px;top:40px;font-family:"Zilla Slab",serif;color:var(--ink)}
  .title-main{font-size:52px;font-weight:700;line-height:1}
  .title-sub{font-size:38px;font-weight:500;line-height:1;margin-top:8px}
  .contact{position:absolute;right:70px;top:81px;text-align:right;font-family:"Zilla Slab",serif}
  .contact-line{font-size:19px;font-weight:700;color:var(--orange)}
  .contact-url{font-size:15px;font-weight:600;color:#333;margin-top:14px}

  .comparison{position:absolute;left:63px;top:213px;display:grid;
    grid-template-columns:288px repeat(4,188px);column-gap:7px;row-gap:7px;
    grid-template-rows:29px 70px repeat(11,33.5px)}
  .col-head{display:flex;align-items:center;padding-left:10px;font-family:"Zilla Slab",serif;font-weight:700;font-size:15px;color:var(--white);white-space:nowrap}
  .col-info{background:var(--white);margin-top:-7px;padding:5px 8px 0 5px;font-size:6.6px;color:#444}
  .col-info .grade-title{text-align:right;font-family:"Zilla Slab",serif;font-weight:700;font-size:7px;padding-bottom:3px;border-bottom:1px solid;margin:0 -8px 5px -5px;padding-right:12px}
  .col-info ul{list-style:none}
  .col-info li{display:flex;justify-content:space-between;margin-bottom:5px;padding-left:8px;position:relative;line-height:9px}
  .col-info li.bullet::before{content:"";position:absolute;left:0;top:3px;width:3px;height:3px;border-radius:50%;background:var(--orange)}
  .col-info li b{width:40px;font-weight:700}
  .is-orange{background:var(--orange)}
  .is-teal{background:var(--teal)}
  .grade-orange{color:var(--orange);border-color:var(--orange)}
  .grade-teal{color:var(--teal);border-color:var(--teal)}
  .row-label{background:var(--label);color:var(--white);font-family:"Zilla Slab",serif;font-weight:600;font-size:14px;letter-spacing:.3px;display:flex;align-items:center;padding-left:20px;padding-bottom:3px}
  .cell{display:flex;align-items:center;justify-content:center}
  .tick{width:30px;height:24px}
  .spacer{background:transparent}
  .disclaimer{position:absolute;left:110px;top:783px;width:980px;text-align:center;font-size:13.5px;line-height:16px;color:#333}
  .paren{position:absolute;top:774px;font-size:42px;line-height:1;color:var(--orange);font-weight:400}
</style>
</head>
<body>
<svg width="0" height="0" style="position:absolute">
  <symbol id="tick" viewBox="0 0 30 24"><path d="M3 13 L11 20 L27 4" fill="none" stroke="#fff" stroke-width="5.5" stroke-linecap="round" stroke-linejoin="round"/></symbol>
</svg>

<header class="masthead">
  <div class="brand"><span class="brand-mark"></span><span class="brand-name">stride</span></div>
  <div class="brand-tagline">Move freely again.</div>
  <div class="title">
    <div class="title-main">Knee OA</div>
    <div class="title-sub">Treatment Comparison</div>
  </div>
  <div class="contact">
    <div class="contact-line">Alderbrook’s Knee Pain Experts</div>
    <div class="contact-url">www.stridekneeclinic.com</div>
  </div>
</header>

<main class="comparison">
  <div class="spacer"></div>
  <div class="col-head is-orange">Hyaluronic Acid (HA)</div>
  <div class="col-head is-teal">Platelet RichPlasma (PRP)</div>
  <div class="col-head is-orange">Stem Cell Therapy &amp; PRP</div>
  <div class="col-head is-teal">Knee Brace(s)</div>

  <div class="spacer"></div>
  <div class="col-info"><div class="grade-title grade-orange">OA Grade</div><ul>
    <li class="bullet"><span>Single Injection (Lubrivo)</span><b>1,2,3,4</b></li>
    <li class="bullet"><span>Single Injection (Synvera)</span><b>1,2,3,4</b></li>
    <li class="bullet"><span>3 Part Injection Series (Trivexa)</span><b>1,2,3,4</b></li>
    <li class="bullet"><span>3/4 Part Injection Series (Kinosyn)</span><b>1,2,3,4</b></li></ul></div>
  <div class="col-info"><div class="grade-title grade-teal">OA Grade</div><ul>
    <li class="bullet"><span>Single Injection (Cellora)</span><b>1, 2</b></li>
    <li class="bullet"><span>2 Part Injection Series</span><b>2, 3</b></li></ul></div>
  <div class="col-info"><div class="grade-title grade-teal">OA Grade</div><ul>
    <li class="bullet"><span>Single Injection</span><b>1, 2, 3, 4</b></li></ul></div>
  <div class="col-info"><div class="grade-title grade-teal">OA Grade</div><ul>
    <li class="bullet"><span>Aligna 2</span><b>1, 2, 3, 4</b></li>
    <li><span>Patellar Stabilization</span><b>1, 2, 3, 4</b></li></ul></div>

  <div class="row-label">Cushion &amp; Lubricate</div>
  <div class="cell is-orange"><svg class="tick"><use href="#tick"/></svg></div>
  <div class="cell is-teal"><svg class="tick"><use href="#tick"/></svg></div>
  <div class="cell is-orange"><svg class="tick"><use href="#tick"/></svg></div>
  <div class="cell is-teal"></div>

  <div class="row-label">Decrease Inflammation</div>
  <div class="cell is-orange"><svg class="tick"><use href="#tick"/></svg></div>
  <div class="cell is-teal"><svg class="tick"><use href="#tick"/></svg></div>
  <div class="cell is-orange"><svg class="tick"><use href="#tick"/></svg></div>
  <div class="cell is-teal"></div>

  <div class="row-label">Stimulates Synovial Production of HA</div>
  <div class="cell is-orange"><svg class="tick"><use href="#tick"/></svg></div>
  <div class="cell is-teal"><svg class="tick"><use href="#tick"/></svg></div>
  <div class="cell is-orange"><svg class="tick"><use href="#tick"/></svg></div>
  <div class="cell is-teal"></div>

  <div class="row-label">Healing Properties</div>
  <div class="cell is-orange"></div>
  <div class="cell is-teal"><svg class="tick"><use href="#tick"/></svg></div>
  <div class="cell is-orange"><svg class="tick"><use href="#tick"/></svg></div>
  <div class="cell is-teal"></div>

  <div class="row-label">Repairative Properties</div>
  <div class="cell is-orange"></div>
  <div class="cell is-teal"></div>
  <div class="cell is-orange"><svg class="tick"><use href="#tick"/></svg></div>
  <div class="cell is-teal"></div>

  <div class="row-label">Potential Cartilage Regeneration</div>
  <div class="cell is-orange"></div>
  <div class="cell is-teal"></div>
  <div class="cell is-orange"><svg class="tick"><use href="#tick"/></svg></div>
  <div class="cell is-teal"></div>

  <div class="row-label">On Average, Benefits Last 4-6 Months</div>
  <div class="cell is-orange"><svg class="tick"><use href="#tick"/></svg></div>
  <div class="cell is-teal"><svg class="tick"><use href="#tick"/></svg></div>
  <div class="cell is-orange"><svg class="tick"><use href="#tick"/></svg></div>
  <div class="cell is-teal"><svg class="tick"><use href="#tick"/></svg></div>

  <div class="row-label">On Average, Benefits Last 6-12 Months</div>
  <div class="cell is-orange"></div>
  <div class="cell is-teal"><svg class="tick"><use href="#tick"/></svg></div>
  <div class="cell is-orange"><svg class="tick"><use href="#tick"/></svg></div>
  <div class="cell is-teal"><svg class="tick"><use href="#tick"/></svg></div>

  <div class="row-label">On Average, Benefits Last 18+ Months</div>
  <div class="cell is-orange"></div>
  <div class="cell is-teal"></div>
  <div class="cell is-orange"><svg class="tick"><use href="#tick"/></svg></div>
  <div class="cell is-teal"><svg class="tick"><use href="#tick"/></svg></div>

  <div class="row-label">Corrects Biomechanics &amp; Stabilizes Joint</div>
  <div class="cell is-orange"></div>
  <div class="cell is-teal"></div>
  <div class="cell is-orange"></div>
  <div class="cell is-teal"><svg class="tick"><use href="#tick"/></svg></div>

  <div class="row-label">Covered by MOST Insurance</div>
  <div class="cell is-orange"><svg class="tick"><use href="#tick"/></svg></div>
  <div class="cell is-teal"></div>
  <div class="cell is-orange"></div>
  <div class="cell is-teal"><svg class="tick"><use href="#tick"/></svg></div>
</main>

<span class="paren" style="left:100px">(</span>
<p class="disclaimer">Treatment outcomes vary by individual. Treatment benefits and length of efficacy are not guaranteed. In some cases, patient’s do not respond to treatment.<br>Multiple treatments may be recommended or necessary for the best outcomes.</p>
<span class="paren" style="left:1118px">)</span>
</body>
</html>
```